New florist business website design

Number 1 want is an easy to navigate & check out website
Needs to be beautiful and eye catching as well.
This is an online only business (no shop front)
Rustic and blush pinks, neutrals, woods, leaves
Customers need to be able to go onto my website, select something they want to buy but have the option to use a drop down box to change colours of the flowers, or add notes to make changes to the arrangement

Industry/Entity Type

Florist

Coding

Coded - Design and coding required

Number of Pages Required

5+ page

Colors
f9d9e8
fff2ec
fffefc

Requirements
Must have
• Drop down menu to take you to other pages for Arrangements, bouquets, everlasting arrangements, gifts, contact
Be able to purchase and “add to basket”
Checkout page
Nice to have
• Be able to add my own photos once I’ve taken new ones
Should not have
• Tacky images or clip art

```html
<!DOCTYPE html>
<html lang="en">
<head>
<meta charset="utf-8">
<title>Fern &amp; Bloom — Florist</title>
<link href="https://fonts.googleapis.com/css2?family=Poppins:wght@300;400;500&family=Playball&family=Playfair+Display:wght@500&family=Cormorant+Garamond:ital@1&display=swap" rel="stylesheet">
<style>
:root{
  --ink:#1c1c1c;
  --muted:#555;
  --line:#3a3a3a;
  --blush:#f9d9e8;
  --blush-soft:#fdeff3;
  --cream:#fff2ec;
  --paper:#fffefc;
  --grey:#f2f2f2;
  --price:#e0245e;
  --btn:#fbeff0;
}
*{margin:0;padding:0;box-sizing:border-box}
html,body{width:1200px;height:3783px;overflow:hidden;background:#fff;font-family:"Poppins",sans-serif;color:var(--ink)}
.page{position:relative;width:1200px;height:3783px}
.abs{position:absolute}
.hero{left:0;top:0;width:1200px;height:640px;background:linear-gradient(90deg,#f4f2f4 0%,#e9e5ea 60%,#dcd8dd 100%)}
.hero-photo{left:676px;top:132px;width:524px;height:508px;background:radial-gradient(ellipse at 45% 35%,#f2c4cb 0%,#b9cdb0 35%,#8da486 55%,rgba(220,216,221,0) 75%)}
.brand{display:flex;align-items:center;gap:10px;font-size:26px;font-weight:400;color:var(--ink)}
.brand .dot{width:14px;height:14px;border-radius:50%;background:var(--blush)}
.nav{left:418px;top:82px;display:flex;gap:0;font-size:13.5px}
.nav a{color:var(--ink);text-decoration:none;margin-right:21px}
.nav a:last-child{margin-right:0}
.basket{left:871px;top:15px;width:156px;height:50px;border:1.5px solid var(--line);border-radius:5px;background:var(--btn);display:flex;align-items:center;justify-content:center;gap:9px;font-size:13px}
.hero-title{left:172px;top:248px;font-family:"Playball",cursive;font-size:60px;font-weight:400}
.rule{height:2px;background:var(--ink)}
.hero-text{left:172px;top:370px;width:470px;font-size:14px;line-height:23px;text-align:justify}
.btn{border:1.5px solid var(--line);border-radius:6px;background:var(--btn);display:flex;align-items:center;justify-content:center;font-size:14.5px;letter-spacing:.5px}
.promo{border:1px solid var(--line);overflow:hidden}
.promo .ph{position:absolute;inset:0}
.promo h3{position:absolute;left:18px;top:20px;font-family:"Playball",cursive;font-size:30px;font-weight:400;line-height:36px}
.promo .btn{position:absolute;left:18px;top:110px;width:104px;height:48px;font-size:13px}
.section-title{left:0;width:1200px;text-align:center;font-size:29px;font-weight:400;letter-spacing:.5px}
.section-sub{left:0;width:1200px;text-align:center;font-size:13px;color:var(--muted)}
.card{border:1.5px solid var(--line);background:#fff;text-align:center}
.card .img{position:absolute;left:50%;transform:translateX(-50%);top:28px;width:140px;height:138px;border-radius:50% 50% 40% 40%}
.card .name{position:absolute;left:0;right:0;top:196px;font-size:14.5px;line-height:24px}
.card .price{position:absolute;left:0;right:0;top:254px;font-family:"Playfair Display",serif;font-size:20px;font-weight:500;color:var(--price)}
.quote-band{left:0;top:1567px;width:1200px;height:375px;background:linear-gradient(120deg,#3b332e 0%,#5a4a44 40%,#4b3e3a 70%,#2f2a27 100%)}
.quote{left:0;top:1670px;width:1200px;text-align:center;font-family:"Playball",cursive;font-size:40px;line-height:57px;color:#fff}
.blog-bg{left:0;top:2559px;width:1200px;height:514px;background:var(--blush-soft)}
.post{border:1px solid #d9d0d3;background:#fff;text-align:center}
.post .img{position:absolute;left:0;top:0;right:0;height:263px}
.post h4{position:absolute;left:0;right:0;top:282px;font-size:15px;font-weight:400}
.post time{position:absolute;left:0;right:0;top:315px;font-size:13px;color:var(--muted)}
.news-bg{left:0;top:3073px;width:1200px;height:317px;background:var(--grey)}
.news-title{left:0;top:3146px;width:1200px;text-align:center;font-size:31px;font-weight:500;letter-spacing:.5px}
.news-sub{left:0;top:3201px;width:1200px;text-align:center;font-size:13.5px}
.news-input{left:376px;top:3260px;width:448px;height:55px;background:#fff;display:flex;align-items:center;padding-left:18px;font-family:"Cormorant Garamond",serif;font-style:italic;font-size:17px;color:#888}
.news-btn{left:702px;top:3268px;width:112px;height:39px;background:var(--ink);color:#fff;font-size:11px;font-weight:500;letter-spacing:1px;display:flex;align-items:center;justify-content:center}
.foot-col{font-size:13.5px;line-height:26.3px;color:var(--ink)}
.pay{display:flex;gap:10px}
.pay span{width:24px;height:14px;border-radius:2px}
.copy{left:0;top:3715px;width:1200px;text-align:center;font-size:13.5px}
</style>
</head>
<body>
<div class="page">

  <header class="abs hero">
    <div class="abs hero-photo" role="img" aria-label="Hand holding a bouquet of pink roses, succulents and eucalyptus tied with ribbon"></div>
    <div class="abs brand" style="left:172px;top:74px"><span class="dot"></span>Fern &amp; Bloom</div>
    <div class="abs basket">
      <svg width="20" height="22" viewBox="0 0 20 22" fill="none" stroke="#1c1c1c" stroke-width="1.6"><path d="M3 6h14l-1 15H4z"/><path d="M6.5 8V5a3.5 3.5 0 0 1 7 0v3"/></svg>
      ADD TO BASKET
    </div>
    <nav class="abs nav">
      <a>Home</a><a>About</a><a>Arrangements</a><a>Bouquets</a><a>Everlasting Arrangements</a><a>Gifts</a><a>Contact</a>
    </nav>
    <h1 class="abs hero-title">Fern Bloom</h1>
    <div class="abs rule" style="left:172px;top:335px;width:118px"></div>
    <p class="abs hero-text">Duis aute irure dolor in reprehenderit in voluptate velit esse cillum dolore eu fugiat nulla pariatur.</p>
    <div class="abs btn" style="left:172px;top:444px;width:123px;height:57px">READ MORE</div>
  </header>

  <section>
    <div class="abs promo" style="left:172px;top:705px;width:417px;height:238px">
      <div class="ph" role="img" aria-label="Florist arranging a bouquet at her workbench" style="background:linear-gradient(90deg,#f8f2ef 0%,#e8dbd3 45%,#8a6b5c 70%,#5d4b3f 100%)"></div>
      <h3>Order &amp; Book<br>Flowers</h3>
      <div class="btn">READ MORE</div>
    </div>
    <div class="abs promo" style="left:611px;top:705px;width:416px;height:238px">
      <div class="ph" role="img" aria-label="Florist in an apron working with fresh flowers in a bright shop" style="background:linear-gradient(90deg,#fbfaf9 0%,#eee9e5 45%,#c7b39f 65%,#ece7e1 100%)"></div>
      <h3>Fresh<br>Flowers</h3>
      <div class="btn">READ MORE</div>
    </div>
  </section>

  <section>
    <h2 class="abs section-title" style="top:1036px">POPULAR PRODUCTS</h2>
    <div class="abs rule" style="left:547px;top:1093px;width:66px"></div>
    <p class="abs section-sub" style="top:1119px">At vero eos et accusamus et iusto od lorem ipsum gnissimos ducimus bland.</p>
    <div class="abs card" style="left:172px;top:1178px;width:201px;height:291px"><div class="img" role="img" aria-label="Bouquet of pink and purple flowers" style="background:radial-gradient(circle,#d9488f 0%,#a45aa5 45%,#5e8a45 75%,rgba(255,255,255,0) 76%)"></div><div class="name">EXCEPTEUR SINT<br>OCCAECAT</div><div class="price">$50</div></div>
    <div class="abs card" style="left:391px;top:1178px;width:200px;height:291px"><div class="img" role="img" aria-label="Bouquet of pink gerberas and white daisies" style="background:radial-gradient(circle,#e94f8c 0%,#f0e4ea 40%,#5f8d47 75%,rgba(255,255,255,0) 76%)"></div><div class="name">EXCEPTEUR SINT<br>OCCAECAT</div><div class="price">$50</div></div>
    <div class="abs card" style="left:608px;top:1178px;width:200px;height:291px"><div class="img" role="img" aria-label="Bouquet of yellow lilies and greenery" style="background:radial-gradient(circle,#e8c52a 0%,#b9a530 40%,#4f7635 75%,rgba(255,255,255,0) 76%)"></div><div class="name">EXCEPTEUR SINT<br>OCCAECAT</div><div class="price">$50</div></div>
    <div class="abs card" style="left:826px;top:1178px;width:201px;height:291px"><div class="img" role="img" aria-label="Bouquet of magenta and lilac flowers" style="background:radial-gradient(circle,#d33c8e 0%,#b58bc2 45%,#6a9a50 75%,rgba(255,255,255,0) 76%)"></div><div class="name">EXCEPTEUR SINT<br>OCCAECAT</div><div class="price">$50</div></div>
  </section>

  <section>
    <div class="abs quote-band" role="img" aria-label="Florist's worktable scattered with flowers, scissors and a small open sign"></div>
    <p class="abs quote">A flower cannot blossom without sunshine,<br>and man cannot live<br>without love ...</p>
  </section>

  <section>
    <h2 class="abs section-title" style="top:2030px">TOP PRODUCTS</h2>
    <div class="abs rule" style="left:547px;top:2087px;width:66px"></div>
    <p class="abs section-sub" style="top:2113px">At vero eos et accusamus et iusto od lorem ipsum gnissimos ducimus bland.</p>
    <div class="abs card" style="left:172px;top:2173px;width:201px;height:289px"><div class="img" role="img" aria-label="Bouquet of pink roses" style="background:radial-gradient(circle,#f2a7b5 0%,#e58a9c 40%,#4f7a3e 75%,rgba(255,255,255,0) 76%)"></div><div class="name">EXCEPTEUR SINT<br>OCCAECAT</div><div class="price">$50</div></div>
    <div class="abs card" style="left:391px;top:2173px;width:200px;height:289px"><div class="img" role="img" aria-label="Bouquet of white and green flowers" style="background:radial-gradient(circle,#f1f0df 0%,#d4d99a 40%,#5f8a45 75%,rgba(255,255,255,0) 76%)"></div><div class="name">EXCEPTEUR SINT<br>OCCAECAT</div><div class="price">$50</div></div>
    <div class="abs card" style="left:608px;top:2173px;width:200px;height:289px"><div class="img" role="img" aria-label="Bouquet of orange and yellow flowers" style="background:radial-gradient(circle,#f29a1e 0%,#e8c032 40%,#557c3a 75%,rgba(255,255,255,0) 76%)"></div><div class="name">EXCEPTEUR SINT<br>OCCAECAT</div><div class="price">$50</div></div>
    <div class="abs card" style="left:826px;top:2173px;width:201px;height:289px"><div class="img" role="img" aria-label="Bouquet of deep red roses" style="background:radial-gradient(circle,#b81e35 0%,#8e1b2e 40%,#3f6633 75%,rgba(255,255,255,0) 76%)"></div><div class="name">EXCEPTEUR SINT<br>OCCAECAT</div><div class="price">$50</div></div>
  </section>

  <section>
    <div class="abs blog-bg"></div>
    <article class="abs post" style="left:172px;top:2638px;width:273px;height:354px"><div class="img" role="img" aria-label="Florist holding a vase of orange tulips" style="background:linear-gradient(135deg,#7a2a28 0%,#d9733d 50%,#567a3a 100%)"></div><h4>Nemo enim ipsam voluptatem</h4><time>14 January, 2021</time></article>
    <article class="abs post" style="left:464px;top:2638px;width:272px;height:354px"><div class="img" role="img" aria-label="Florist trimming stems at a shop counter" style="background:linear-gradient(135deg,#9c6e56 0%,#cfc6bf 50%,#5f7d4a 100%)"></div><h4>Nemo enim ipsam voluptatem</h4><time>14 January, 2021</time></article>
    <article class="abs post" style="left:755px;top:2638px;width:272px;height:354px"><div class="img" role="img" aria-label="Florist in a blue apron among colourful flowers" style="background:linear-gradient(135deg,#c23a52 0%,#e9d8cf 50%,#4e78a8 100%)"></div><h4>Nemo enim ipsam voluptatem</h4><time>14 January, 2021</time></article>
  </section>

  <section>
    <div class="abs news-bg"></div>
    <h2 class="abs news-title">SUBSCRIBE TO OUR NEWSLETTER</h2>
    <p class="abs news-sub">Sign up for our email list and get 15% off your first order</p>
    <div class="abs news-input">Your email</div>
    <div class="abs news-btn">SUBSCRIBE</div>
  </section>

  <footer>
    <div class="abs brand" style="left:172px;top:3532px;font-size:30px"><span class="dot"></span>Fern &amp; Bloom</div>
    <div class="abs foot-col" style="left:472px;top:3488px">Home<br>About<br>Blog<br>Pricing<br>Contact</div>
    <div class="abs foot-col" style="left:607px;top:3488px">Nemo enim ipsam<br>Voluptatem quia<br>Voluptas sit<br>Aspernatur aut odit<br>Aut fugit</div>
    <div class="abs foot-col" style="left:829px;top:3488px">Nemo enim ipsam<br>Voluptatem quia</div>
    <div class="abs pay" style="left:829px;top:3577px">
      <span style="background:#d8dbe6"></span><span style="background:#f0c9a6"></span><span style="background:#a9c2e3"></span><span style="background:#cfd6ea"></span><span style="background:#d6e3ef"></span><span style="background:#f1e2c4"></span>
    </div>
    <div class="abs" style="left:172px;top:3687px;width:855px;height:1px;background:#ddd"></div>
    <p class="abs copy">Copyrights @ 2021 Fern Bloom. All Rights Reserved.</p>
  </footer>

</div>
</body>
</html>
```